Website Design for Forklift Training Company

DO NOT CONTACT PRIVATELY. ONLY SUBMISSIONS HERE WILL BE CONSIDERED

I need a design for a website that offers forklift training courses.

The company offers accredited, onsite forklift training that are customized for the needs of each individual company. The company offers a variety of courses to operate forklifts and other machinary.

About: "KVW Training Ltd delivers bespoke onsite forklift truck operator training throught the uk.
All our instructors have a wealth of knowledge and expertise to provide your company with all your forklift truck training requirements.
KVW Training Ltd is registered and accredited by plomvex standards so you can be rest assured that all forklift training is carried out the very highest standard"

I need the following pages designed:
> a) Home Page: Include a header image, ways to contact, about snippet, overview of courses, accreditation that will be received after completing the courses. (See attachments for samples)
> b) About Page
> c) Contact Us Page
> d) Course Page Template: A page that will be used as template for the courses offered. It should contain;
1. Cover image for the course
2. A description of the course
3. A table indicating the various course options
4. Course Objectives
5. What the trainee will receive after doing the course (example: a certification)

Industrial Businesses

4 page

Colors
0054AA
0677BA
7BADD7
CADEEF
E8F1F8
0094D4
00A9DD
6FCCEA
C7EBF8
E9F6FB

• - No Search bar

```html
<!DOCTYPE html>
<html lang="en">
<head>
<meta charset="utf-8">
<title>KVW Training Ltd – Onsite Forklift Training</title>
<link href="https://fonts.googleapis.com/css2?family=Montserrat:wght@600;700;800&family=Roboto:wght@400;500;700&display=swap" rel="stylesheet">
<style>
:root{
  --navy:#0054AA;
  --blue:#0677BA;
  --sky:#00A9DD;
  --sky-2:#0094D4;
  --nav:#1BA8DF;
  --pale:#E9F6FB;
  --ink:#1d1d1d;
  --text:#666;
  --white:#fff;
  --line:#e6e6e6;
}
*{box-sizing:border-box;margin:0;padding:0}
html,body{width:1200px;height:3624px;overflow:hidden}
body{position:relative;background:var(--white);font-family:'Roboto',sans-serif;color:var(--ink)}
.abs{position:absolute}
.head{font-family:'Montserrat',sans-serif;font-weight:700}

.brand{left:110px;top:10px;height:62px;display:flex;align-items:center;gap:10px}
.brand-mark{width:62px;height:62px;background:#111}
.brand-name{font-family:'Montserrat',sans-serif;font-weight:800;font-size:22px;color:var(--ink);letter-spacing:-.5px}
.call{left:722px;top:14px;display:flex;gap:14px}
.icon-circle{width:32px;height:32px;border-radius:50%;background:var(--blue);display:flex;align-items:center;justify-content:center;margin-top:8px}
.call small,.follow small{display:block;font-size:11px;font-weight:700;color:var(--ink)}
.call strong{display:block;font-size:21px;font-weight:500;color:var(--sky-2);margin-top:4px}
.follow{left:966px;top:14px}
.socials{display:flex;gap:8px;margin-top:8px}
.socials span{width:24px;height:24px;border-radius:50%;background:var(--navy)}

.nav{left:0;top:76px;width:1200px;height:47px;background:var(--nav);display:flex;justify-content:center;align-items:center;gap:26px;color:#fff;font-size:13px;font-weight:700}

.hero{left:0;top:123px;width:1200px;height:558px;background:linear-gradient(90deg,#8a9bb4 0%,#c3cad6 45%,#b8a88a 62%,#9ea7b5 100%)}
.hero-tag{left:111px;top:298px;width:225px;height:72px;background:var(--navy);color:#fff;font-size:46px;display:flex;align-items:center;justify-content:center}
.hero-title{left:108px;top:378px;font-size:46px;color:#fff;text-shadow:0 2px 6px rgba(0,0,0,.3)}
.scroll-down{left:570px;top:651px;width:60px;height:60px;border-radius:50%;background:#fff;border:3px solid #e2e2e2;display:flex;align-items:center;justify-content:center}

.about-frame{left:108px;top:838px;width:318px;height:376px;border:2px solid var(--sky)}
.about-main{left:123px;top:856px;width:297px;height:339px;background:linear-gradient(160deg,#d9c9ab,#b79c70 50%,#e8b832 80%,#8a8a8a)}
.about-s1{left:425px;top:822px;width:205px;height:200px;background:linear-gradient(160deg,#b9ab92,#8d7f69 60%,#d6632c)}
.about-s2{left:425px;top:1030px;width:205px;height:201px;background:linear-gradient(160deg,#c9a98a,#d08d2c 55%,#3a3a3a)}
.about-title{left:718px;top:852px;font-size:34px;color:var(--ink)}
.about-text{left:718px;top:912px;width:372px;font-size:14px;line-height:25.7px;color:var(--text)}
.btn{display:flex;align-items:center;justify-content:center;gap:10px;background:var(--navy);color:#fff;font-size:13px;font-weight:700;border-radius:3px}
.about-btn{left:718px;top:1145px;width:156px;height:47px}

.courses-band{left:0;top:1348px;width:1200px;height:305px;background:var(--navy)}
.courses-title{left:0;top:1398px;width:1200px;text-align:center;font-size:34px;color:#fff}
.courses-intro{left:155px;top:1455px;width:890px;text-align:center;color:#fff;font-size:13.5px;line-height:22.5px}
.course-photo{top:1574px;width:318px;height:220px}
.course-card{top:1754px;width:296px;height:179px;background:#fff;box-shadow:0 2px 8px rgba(0,0,0,.12);padding:18px 26px}
.course-card h3{font-family:'Montserrat',sans-serif;font-size:14px;font-weight:700;color:var(--ink);margin-bottom:16px}
.course-card li{list-style:none;display:flex;align-items:center;gap:13px;font-size:13px;color:var(--text);height:25px}
.tick{width:12px;height:12px;border-radius:50%;background:var(--sky-2);display:flex;align-items:center;justify-content:center;flex:none}
.more{display:flex;align-items:center;gap:8px;color:var(--sky-2);font-size:11px;font-weight:700;margin-top:12px}
.more-dot{width:11px;height:11px;border-radius:50%;background:currentColor;display:flex;align-items:center;justify-content:center}

.divider{left:0;top:2017px;width:1200px;height:1px;background:var(--line)}

.acc-title{left:0;top:2084px;width:1200px;text-align:center;font-size:26px;color:var(--ink)}
.acc-card{top:2174px;width:490px;height:420px;background:#fff;box-shadow:0 0 6px rgba(0,0,0,.12);padding:10px}
.acc-inner{width:100%;height:100%;border:2px solid var(--navy);display:flex;flex-direction:column;align-items:center;padding:38px 30px 0}
.acc-card.alt .acc-inner{border-color:var(--sky)}
.badge{width:86px;height:92px}
.acc-inner p{margin-top:33px;text-align:center;font-size:14px;line-height:25px;color:var(--text)}
.acc-inner .more{margin-top:20px;font-size:12px;color:var(--navy);text-decoration:underline}
.acc-card.alt .more{color:var(--sky-2)}

.contact{left:0;top:2697px;width:1200px;height:676px;background:linear-gradient(180deg,#3bb8e6,#22a6de 60%,#30b0e2)}
.contact-title{left:0;top:2770px;width:1200px;text-align:center;font-size:40px;color:#fff}
.field{background:#fff;border-radius:2px;padding:0 20px;display:flex;align-items:center;font-size:14px;color:#777}
.field.msg{align-items:flex-start;padding-top:16px}
.submit{left:525px;top:3105px;width:148px;height:48px}
.info-icon{top:3222px;width:57px;height:57px;border-radius:50%;background:#fff;display:flex;align-items:center;justify-content:center}
.info{top:3222px;color:#fff;font-size:14px;line-height:21px}
.info b{display:block;font-size:13px;font-weight:700;margin-bottom:6px}

.footer{left:0;top:3373px;width:1200px;height:251px;background:var(--navy)}
.foot-brand{left:0;top:3421px;width:1200px;display:flex;justify-content:center;align-items:center;gap:8px}
.foot-brand .brand-mark{width:56px;height:54px}
.foot-brand .brand-name{color:#fff;font-size:20px}
.foot-nav{top:3488px;background:none;height:24px}
.copy{left:0;top:3540px;width:1200px;text-align:center;color:#fff;font-size:14px}
</style>
</head>
<body>

<div class="abs brand"><span class="brand-mark"></span><span class="brand-name">KVW TRAINING LTD</span></div>
<div class="abs call">
  <span class="icon-circle"><svg width="14" height="14" viewBox="0 0 24 24"><path fill="#fff" d="M6.6 10.8a15 15 0 0 0 6.6 6.6l2.2-2.2c.3-.3.7-.4 1-.2 1.1.4 2.3.6 3.6.6.6 0 1 .4 1 1V20c0 .6-.4 1-1 1A17 17 0 0 1 3 4c0-.6.4-1 1-1h3.5c.6 0 1 .4 1 1 0 1.3.2 2.5.6 3.6.1.3 0 .7-.2 1z"/></svg></span>
  <div><small>CALL US TODAY</small><strong>07700900123</strong></div>
</div>
<div class="abs follow"><small>FOLLOW US ON</small><div class="socials"><span></span><span></span><span></span><span></span></div></div>

<nav class="abs nav">
  <span>HOME</span><span>|</span><span>FORKLIFT TRAINING COURSES</span><span>|</span><span>ABOUT US</span><span>|</span><span>PRICES</span><span>|</span><span>LINKS</span><span>|</span><span>CONTACT US</span>
</nav>

<div class="abs hero" role="img" aria-label="Yellow forklift carrying a wrapped pallet of boxes inside a warehouse"></div>
<div class="abs hero-tag head">ONSITE</div>
<div class="abs hero-title head">FORKLIFT TRAINING</div>
<div class="abs scroll-down"><svg width="22" height="22" viewBox="0 0 24 24"><path d="M12 4v15M5 12l7 7 7-7" stroke="#0054AA" stroke-width="3.2" fill="none" stroke-linecap="round" stroke-linejoin="round"/></svg></div>

<div class="abs about-frame"></div>
<div class="abs about-main" role="img" aria-label="Supervisor in hi-vis vest beside a yellow forklift in a warehouse aisle"></div>
<div class="abs about-s1" role="img" aria-label="Operator driving an orange forklift between racking"></div>
<div class="abs about-s2" role="img" aria-label="Orange forklift in a storage area"></div>
<h2 class="abs about-title head">ABOUT US</h2>
<p class="abs about-text">KVW Training Ltd delivers bespoke onsite forklift truck operator training throught the uk. All our instructors have a wealth of knowledge and expertise to provide your company with all your forklift truck training requirements. KVW Training Ltd is registered and accredited by plomvex standards so you can be rest assured that all forklift training is carried out the very highest standard KVW Training Ltd delivers bespoke onsite forklift truck</p>
<div class="abs btn about-btn">LEARN MORE <span class="more-dot" style="color:#fff;width:13px;height:13px"><svg width="7" height="7" viewBox="0 0 10 10"><path d="M3 1l4 4-4 4" stroke="#0054AA" stroke-width="2" fill="none"/></svg></span></div>

<div class="abs courses-band"></div>
<h2 class="abs courses-title head">FORKLIFT TRAINING COURSES</h2>
<p class="abs courses-intro">We specialise in onsite forklift training using the equipment and facilities your employees will use in there everyday work wether its counterbalance mountrex cranevo cherry picker to name a few. We also accommodate an anytime any shift training schedule to cater for your different shift patterns.By the time we have finished your staff will be well trained and ready to operate efficiently and safely</p>

<div class="abs course-photo" style="left:99px;background:linear-gradient(160deg,#d8d2c8,#9c8f7c 55%,#e39b2a)" role="img" aria-label="Forklift working among rolls of stock"></div>
<div class="abs course-photo" style="left:442px;background:linear-gradient(160deg,#cfd4da,#b3a89a 50%,#e28a2a)" role="img" aria-label="Operator on an orange forklift in a warehouse"></div>
<div class="abs course-photo" style="left:784px;background:linear-gradient(160deg,#6f6a62,#2f2f2f 50%,#e5a22a)" role="img" aria-label="Row of yellow forklifts parked outdoors"></div>

<div class="abs course-card" style="left:110px">
  <h3>FORKLIFT TRAINING COURSES</h3>
  <ul><li><span class="tick"><svg width="7" height="7" viewBox="0 0 10 10"><path d="M2 5l2 2 4-4" stroke="#fff" stroke-width="2" fill="none"/></svg></span>Vendra Truck Training Course</li>
  <li><span class="tick"><svg width="7" height="7" viewBox="0 0 10 10"><path d="M2 5l2 2 4-4" stroke="#fff" stroke-width="2" fill="none"/></svg></span>Quadlift Training course</li>
  <li><span class="tick"><svg width="7" height="7" viewBox="0 0 10 10"><path d="M2 5l2 2 4-4" stroke="#fff" stroke-width="2" fill="none"/></svg></span>Counterbalance Training Course</li></ul>
  <div class="more">LEARN MORE <span class="more-dot"><svg width="6" height="6" viewBox="0 0 10 10"><path d="M3 1l4 4-4 4" stroke="#fff" stroke-width="2.4" fill="none"/></svg></span></div>
</div>
<div class="abs course-card" style="left:453px">
  <h3>MEWP TRAINING COURSES</h3>
  <ul><li><span class="tick"><svg width="7" height="7" viewBox="0 0 10 10"><path d="M2 5l2 2 4-4" stroke="#fff" stroke-width="2" fill="none"/></svg></span>Cherry Picker Training Course</li>
  <li><span class="tick"><svg width="7" height="7" viewBox="0 0 10 10"><path d="M2 5l2 2 4-4" stroke="#fff" stroke-width="2" fill="none"/></svg></span>Scissor Lift Training Course</li>
  <li><span class="tick"><svg width="7" height="7" viewBox="0 0 10 10"><path d="M2 5l2 2 4-4" stroke="#fff" stroke-width="2" fill="none"/></svg></span>Harness &amp; Lanyard Training Course</li></ul>
  <div class="more">LEARN MORE <span class="more-dot"><svg width="6" height="6" viewBox="0 0 10 10"><path d="M3 1l4 4-4 4" stroke="#fff" stroke-width="2.4" fill="none"/></svg></span></div>
</div>
<div class="abs course-card" style="left:795px">
  <h3>OTHER TRAINING COURSES</h3>
  <ul><li><span class="tick"><svg width="7" height="7" viewBox="0 0 10 10"><path d="M2 5l2 2 4-4" stroke="#fff" stroke-width="2" fill="none"/></svg></span>Bolvant Truck Training Course</li>
  <li><span class="tick"><svg width="7" height="7" viewBox="0 0 10 10"><path d="M2 5l2 2 4-4" stroke="#fff" stroke-width="2" fill="none"/></svg></span>Front Loading Shovel Training Course</li>
  <li><span class="tick"><svg width="7" height="7" viewBox="0 0 10 10"><path d="M2 5l2 2 4-4" stroke="#fff" stroke-width="2" fill="none"/></svg></span>Overhead Pendant Crane Training</li></ul>
  <div class="more">LEARN MORE <span class="more-dot"><svg width="6" height="6" viewBox="0 0 10 10"><path d="M3 1l4 4-4 4" stroke="#fff" stroke-width="2.4" fill="none"/></svg></span></div>
</div>

<div class="abs divider"></div>

<h2 class="abs acc-title head">FORKLIFT TRAINING ACCREDITATION</h2>
<div class="abs acc-card" style="left:99px">
  <div class="acc-inner">
    <div class="badge" style="background:var(--navy)" role="img" aria-label="Accreditation badge"></div>
    <p>PLOMVEX is recognised throughout the united kingdom and Ireland as one of the leading material handling equipment training accrediting bodies. PLOMVEX is a founder member of the CWT (council for workplace transport) and this replaced the accrediting bodies forum previously run by the WSA. They have over 40 years experience of setting training standards,accreditation and monitoring.</p>
    <div class="more">LEARN MORE <span class="more-dot"><svg width="6" height="6" viewBox="0 0 10 10"><path d="M3 1l4 4-4 4" stroke="#fff" stroke-width="2.4" fill="none"/></svg></span></div>
  </div>
</div>
<div class="abs acc-card alt" style="left:610px">
  <div class="acc-inner">
    <div class="badge" style="width:130px;height:92px;border-radius:46px;background:var(--pale)" role="img" aria-label="Workplace transport body badge"></div>
    <p>We are accredited by the PLOMVEX who are recognised by the workplace safety authority as competent to deliver forklift truck operator training courses.As an PLOMVEX accredited training provider we are monitored annually to ensure we are maintaining our high standards as laid down by the PLOMVEX. All our instructors are qualified and registered with the PLOMVEX and monitored.</p>
    <div class="more">LEARN MORE <span class="more-dot"><svg width="6" height="6" viewBox="0 0 10 10"><path d="M3 1l4 4-4 4" stroke="#fff" stroke-width="2.4" fill="none"/></svg></span></div>
  </div>
</div>

<div class="abs contact" role="img" aria-label="Blue tinted warehouse with forklift in the background"></div>
<h2 class="abs contact-title head">CONTACT US</h2>
<div class="abs field" style="left:227px;top:2869px;width:369px;height:49px">Name</div>
<div class="abs field" style="left:604px;top:2869px;width:369px;height:49px">Company</div>
<div class="abs field" style="left:227px;top:2929px;width:369px;height:49px">Email</div>
<div class="abs field" style="left:604px;top:2929px;width:369px;height:49px">Telephone</div>
<div class="abs field msg" style="left:227px;top:2989px;width:746px;height:96px">Message</div>
<div class="abs btn submit">SUBMIT NOW <span class="more-dot" style="color:#fff;width:13px;height:13px"><svg width="7" height="7" viewBox="0 0 10 10"><path d="M3 1l4 4-4 4" stroke="#0054AA" stroke-width="2" fill="none"/></svg></span></div>

<div class="abs info-icon" style="left:68px"><svg width="28" height="28" viewBox="0 0 24 24"><path d="M12 2a7 7 0 0 0-7 7c0 5 7 13 7 13s7-8 7-13a7 7 0 0 0-7-7z" stroke="#00A9DD" stroke-width="1.6" fill="none"/><circle cx="12" cy="9" r="2.5" stroke="#00A9DD" stroke-width="1.6" fill="none"/></svg></div>
<div class="abs info" style="left:148px;top:3214px"><b>LOCATION :</b>14 Harrow Lane<br>Kelsby</div>
<div class="abs info-icon" style="left:305px"><svg width="28" height="28" viewBox="0 0 24 24"><rect x="3" y="6" width="18" height="13" rx="1" stroke="#00A9DD" stroke-width="1.6" fill="none"/><path d="M3 7l9 7 9-7" stroke="#00A9DD" stroke-width="1.6" fill="none"/></svg></div>
<div class="abs info" style="left:392px"><b>EMAIL US :</b>info@kvwtraining.co</div>
<div class="abs info-icon" style="left:604px"><svg width="28" height="28" viewBox="0 0 24 24"><path d="M6.6 10.8a15 15 0 0 0 6.6 6.6l2.2-2.2c.3-.3.7-.4 1-.2 1.1.4 2.3.6 3.6.6.6 0 1 .4 1 1V20c0 .6-.4 1-1 1A17 17 0 0 1 3 4c0-.6.4-1 1-1h3.5c.6 0 1 .4 1 1 0 1.3.2 2.5.6 3.6.1.3 0 .7-.2 1z" stroke="#00A9DD" stroke-width="1.5" fill="none"/></svg></div>
<div class="abs info" style="left:690px"><b>CALL US :</b><strong>07700900123</strong></div>
<div class="abs info-icon" style="left:844px"><svg width="28" height="28" viewBox="0 0 24 24"><path d="M6.6 10.8a15 15 0 0 0 6.6 6.6l2.2-2.2c.3-.3.7-.4 1-.2 1.1.4 2.3.6 3.6.6.6 0 1 .4 1 1V20c0 .6-.4 1-1 1A17 17 0 0 1 3 4c0-.6.4-1 1-1h3.5c.6 0 1 .4 1 1 0 1.3.2 2.5.6 3.6.1.3 0 .7-.2 1z" stroke="#00A9DD" stroke-width="1.5" fill="none"/></svg></div>
<div class="abs info" style="left:935px"><b>WORKING HOURS :</b>Mon - Fri &nbsp;: &nbsp;Open 24 Hours<br>Saturday &nbsp;: &nbsp;&nbsp;6:00 - 18:00<br>Sunday &nbsp;&nbsp;&nbsp;&nbsp;: &nbsp;Appointment Only</div>

<footer class="abs footer"></footer>
<div class="abs foot-brand"><span class="brand-mark"></span><span class="brand-name">KVW TRAINING LTD</span></div>
<nav class="abs nav foot-nav">
  <span>HOME</span><span>|</span><span>FORKLIFT TRAINING COURSES</span><span>|</span><span>ABOUT US</span><span>|</span><span>PRICES</span><span>|</span><span>LINKS</span><span>|</span><span>CONTACT US</span>
</nav>
<p class="abs copy">© 2021 KVW Training LTD. All Rights Reserved</p>

</body>
</html>
```